Modern & Fresh Vantacor Book Cover

Need a creative e-book cover for my book.

Title: Master Vantacor Fast
Subtitle: Learn How To Easily Choose & Enroll in the Perfect Coverage at the Perfect Time.

Target Market(s)

60-70 year olds in the United States

Font styles to use
Sans Serif

Colors
9bcb3c
33a6d7

Requirements
Must have
• Must look modern and fresh.
• Use our company colors www.Movaquill.com

```html
<!DOCTYPE html>
<html lang="en">
<head>
<meta charset="UTF-8">
<title>Master Vantacor Fast – Book Cover</title>
<link href="https://fonts.googleapis.com/css2?family=Anton&family=Montserrat:wght@400;800&family=Oswald:wght@500&display=swap" rel="stylesheet">
<style>
  :root {
    --brand-blue: #2b79bb;
    --brand-green: #7dad3a;
    --rule-blue: #6aa0cf;
    --ink: #444444;
    --paper: #ffffff;
    --art-pink: #f7a9c8;
    --art-blue: #9fd6f0;
  }
  html, body {
    margin: 0;
    padding: 0;
    width: 800px;
    height: 1200px;
    overflow: hidden;
    background: var(--paper);
  }
  .cover {
    position: relative;
    width: 800px;
    height: 1200px;
    background: var(--paper);
  }
  .title-block {
    position: absolute;
    left: 0;
    top: 0;
    width: 800px;
    height: 610px;
  }
  .title-kicker { font-family: "Montserrat", sans-serif; font-weight: 800; fill: var(--brand-blue); }
  .title-rule { stroke: var(--rule-blue); stroke-width: 4; }
  .title-main { font-family: "Anton", sans-serif; fill: var(--brand-green); }
  .title-accent { font-family: "Anton", sans-serif; fill: var(--brand-blue); }
  .subtitle {
    position: absolute;
    left: 100px;
    top: 618px;
    width: 600px;
    margin: 0;
    text-align: center;
    font-family: "Montserrat", sans-serif;
    font-weight: 400;
    font-size: 20px;
    line-height: 28px;
    letter-spacing: 0.3px;
    color: var(--ink);
  }
  .hero-art {
    position: absolute;
    left: 272px;
    top: 716px;
    width: 232px;
    height: 354px;
    border-radius: 18px;
    background: radial-gradient(circle at 55% 30%, var(--art-pink) 0%, #fbd6e5 45%, #e6f4fb 80%, var(--paper) 100%);
  }
  .author-name {
    position: absolute;
    left: 0;
    top: 1110px;
    width: 800px;
    margin: 0;
    text-align: center;
    font-family: "Oswald", sans-serif;
    font-weight: 500;
    font-size: 44px;
    line-height: 54px;
    letter-spacing: 17px;
    padding-left: 17px;
    color: var(--brand-blue);
  }
</style>
</head>
<body>
  <main class="cover">
    <svg class="title-block" viewBox="0 0 800 610" role="heading" aria-level="1" aria-label="Master Vantacor Fast">
      <line class="title-rule" x1="94" y1="107" x2="225" y2="107"/>
      <line class="title-rule" x1="575" y1="107" x2="706" y2="107"/>
      <text class="title-kicker" x="400" y="142" text-anchor="middle" font-size="98" textLength="330" lengthAdjust="spacingAndGlyphs">MASTER</text>
      <text class="title-main" x="81" y="309" font-size="155" textLength="638" lengthAdjust="spacingAndGlyphs">VANTACOR</text>
      <text class="title-accent" x="81" y="597" font-size="314" textLength="638" lengthAdjust="spacingAndGlyphs">FAST</text>
    </svg>

    <p class="subtitle">Learn How To Easily Choose &amp; Enroll in the Perfect<br>Coverage at the Perfect Time.</p>

    <div class="hero-art" role="img" aria-label="Illustration of a doctor with a clipboard and a woman standing before a large pink heart with a pulse line, surrounded by pill, tooth and syringe icons"></div>

    <p class="author-name">AUTHOR NAME</p>
  </main>
</body>
</html>
```